Marwick Family Chiropractic Stationary

The letterhead and business card must have our logo.
We would like to see the logo used in different ways ( It can be expanded upon in the stationary.)
Please use the the same or similar colors.
Must be eye catching and memorable.
Must be easy to read

Reason: The doctor has been too busy to make any final decisions. He would like to give himself a little more time.

Target Market(s)

Chiropractic Healthcare

Industry/Entity Type

Business

Requirements
Must have
• Dr. Leonard Marwick D.C.
Chiropractor

860-555-0183

417 Birchfield Road, 2nd Floor
Vernon, CT 06091

drmarwick@marwickspine.example
www.marwickspine.example
www.facebook.com/MarwickFamilySpine
Should not have
• should not be difficult to read

```html
<!DOCTYPE html>
<html lang="en">
<head>
<meta charset="utf-8">
<title>Marwick Family Chiropractic – Business Cards</title>
<link rel="stylesheet" href="https://fonts.googleapis.com/css2?family=Montserrat:wght@600&family=Arimo:wght@400;700&display=swap">
<style>
  :root {
    --backdrop: #e2e3e4;
    --ink: #0b0b0b;
    --lime: #a6cf5a;
    --leaf-green: #2c9a48;
    --paper: #ffffff;
    --stone: #a89e8a;
    --card-w: 557px;
    --card-h: 318px;
    --radius: 20px;
  }
  * { box-sizing: border-box; margin: 0; padding: 0; }
  html, body { width: 1200px; height: 740px; overflow: hidden; }
  body {
    background: var(--backdrop);
    font-family: "Arimo", Arial, sans-serif;
    position: relative;
  }
  .card {
    position: absolute;
    width: var(--card-w);
    height: var(--card-h);
    border-radius: var(--radius);
    overflow: hidden;
  }
  .card--front { left: 32px; top: 27px; background: var(--ink); }
  .card--lime  { left: 615px; top: 27px; background: var(--lime); }
  .card--green { left: 32px; top: 384px; background: var(--leaf-green); }
  .card--dark  { left: 615px; top: 384px; background: var(--ink); }

  .swoosh { position: absolute; inset: 0; }

  .doctor {
    position: absolute; right: 32px; top: 17px; text-align: right; color: var(--ink);
  }
  .doctor__name { font-weight: 700; font-size: 15px; letter-spacing: -0.2px; }
  .doctor__title { font-size: 14px; margin-top: 3px; }

  .brand-mark {
    position: absolute; border-radius: 50%;
  }
  .card--front .brand-mark {
    left: 78px; top: 78px; width: 110px; height: 110px; background: #5c5548;
  }
  .brand-name {
    font-family: "Montserrat", sans-serif; font-weight: 600; color: var(--lime);
    text-align: center; position: absolute;
  }
  .card--front .brand-name { left: 10px; width: 246px; top: 200px; }
  .brand-name__main { display: block; font-size: 38px; line-height: 1; letter-spacing: 1px; }
  .brand-name__sub { display: block; font-size: 14.5px; margin-top: 6px; letter-spacing: 0.6px; }

  .divider {
    position: absolute; left: 302px; top: 152px; width: 1px; height: 140px; background: #5a5a5a;
  }
  .contact {
    position: absolute; left: 328px; top: 162px; color: var(--paper); font-size: 12.5px; list-style: none;
  }
  .contact li { display: flex; align-items: center; gap: 6px; height: 19px; }
  .contact svg { width: 11px; height: 11px; flex: none; }
  .address { position: absolute; left: 328px; top: 259px; color: var(--paper); font-size: 12.5px; line-height: 19px; }

  .card--lime .brand-mark, .card--green .brand-mark {
    left: 198px; top: 42px; width: 160px; height: 160px; background: var(--paper);
  }
  .url {
    position: absolute; left: 0; right: 0; text-align: center; color: var(--paper);
    font-size: 15px; letter-spacing: 2.6px;
  }
  .card--lime .url, .card--green .url { top: 250px; }

  .card--dark .brand-mark {
    left: 178px; top: 22px; width: 200px; height: 200px; background: #1c231a;
  }
  .card--dark .brand-name { left: 0; right: 0; top: 92px; }
  .card--dark .brand-name__main { font-size: 66px; letter-spacing: 2px; }
  .card--dark .brand-name__sub { font-size: 25px; margin-top: 6px; letter-spacing: 1.5px; }
  .card--dark .url { top: 262px; }
</style>
</head>
<body>

<section class="card card--front" aria-label="Business card front">
  <svg class="swoosh" viewBox="0 0 557 318" aria-hidden="true">
    <path d="M0,0 H557 V168 C430,84 250,24 0,56 Z" fill="var(--lime)"/>
    <path d="M0,56 C250,24 430,84 557,168 V188 C430,98 250,36 0,64 Z" fill="var(--leaf-green)"/>
  </svg>
  <div class="doctor">
    <p class="doctor__name">Dr. Leonard Marwick D.C.</p>
    <p class="doctor__title">Chiropractor</p>
  </div>
  <span class="brand-mark"></span>
  <p class="brand-name">
    <span class="brand-name__main">MARWICK</span>
    <span class="brand-name__sub">FAMILY CHIROPRACTIC</span>
  </p>
  <span class="divider"></span>
  <ul class="contact">
    <li><svg viewBox="0 0 12 12"><path d="M3 1 L5 3.5 L4 5 Q5.5 7.5 7 8 L8.5 7 L11 9 L9.5 11 Q3 10 1 2.5 Z" fill="#fff"/></svg>860-555-0183</li>
    <li><svg viewBox="0 0 12 12"><rect width="12" height="12" rx="1.5" fill="#3b5ba0"/></svg>MarwickFamilySpine</li>
    <li><svg viewBox="0 0 12 12"><circle cx="6" cy="6" r="5" fill="none" stroke="#fff" stroke-width="1.3"/><path d="M1 6 H11 M6 1 V11" stroke="#fff" stroke-width="1"/></svg>www.marwickspine.example</li>
    <li><svg viewBox="0 0 12 12"><rect x="0.7" y="2.5" width="10.6" height="7.5" fill="none" stroke="#fff" stroke-width="1.2"/><path d="M1 3 L6 7 L11 3" fill="none" stroke="#fff" stroke-width="1.2"/></svg>mymarwick@marwickspine.example</li>
  </ul>
  <p class="address">417 Birchfield Road<br>2nd Floor, Vernon, CT 06091</p>
</section>

<section class="card card--lime" aria-label="Business card back, light green">
  <span class="brand-mark"></span>
  <p class="url">www.marwickspine.example</p>
</section>

<section class="card card--green" aria-label="Business card back, green">
  <span class="brand-mark"></span>
  <p class="url">www.marwickspine.example</p>
</section>

<section class="card card--dark" aria-label="Business card back, black">
  <span class="brand-mark"></span>
  <p class="brand-name">
    <span class="brand-name__main">MARWICK</span>
    <span class="brand-name__sub">FAMILY CHIROPRACTIC</span>
  </p>
  <p class="url">www.marwickspine.example</p>
</section>

</body>
</html>
```